Banner ads for LP that work with same theme as below banners

Love the banner ads below. Need more with attached photos. But use the same wording, font as in below banner ads. Should be LP size 1200/627 so I can use for Pixorly and LP. Looking for great ads to use as LP ads. We do lots of ads so it will be worth your time to enter this contest you will be rewarded with a ton of work. Need several banner ads that work together. So maybe 1 of the dresses, 1 of the sweater, 1 of the leggings, 1 of the jacket

Target Market(s)

Women 24-45

Industry/Entity Type

Fashion

Requirements
Must have
• Banner ads that work for LP and Pixorly
Nice to have
• Several options to choose from
Should not have
• not sure

```html
<!DOCTYPE html>
<html lang="en">
<head>
<meta charset="utf-8">
<title>Our Best Sweater Ever – Banner</title>
<link rel="stylesheet" href="https://fonts.googleapis.com/css2?family=Playball&family=Old+Standard+TT:wght@400;700&display=swap">
<style>
  :root {
    --bg: #ece8e3;
    --bg-shade: #e2ddd7;
    --ghost-text: #ddd8d2;
    --script-red: #d3282a;
    --headline-green: #1f3516;
    --button-black: #1c1a1a;
    --button-text: #ffffff;
    --flora-orange: #e07a2a;
    --flora-yellow: #e8b53a;
    --flora-green: #6f8f4a;
    --photo-light: #d8d4dc;
    --photo-mid: #b9b6bd;
    --photo-dark: #4a3b33;
  }
  * { margin: 0; padding: 0; box-sizing: border-box; }
  html, body { width: 1200px; height: 627px; overflow: hidden; background: var(--bg); }
  .banner {
    position: relative;
    width: 1200px;
    height: 627px;
    overflow: hidden;
    background:
      repeating-linear-gradient(135deg, var(--bg) 0 14px, var(--bg-shade) 14px 15px);
  }
  .floral-border {
    position: absolute;
    left: 0; top: 0;
    width: 1200px; height: 108px;
    background: linear-gradient(180deg,
      rgba(224,122,42,0.55) 0%,
      rgba(232,181,58,0.45) 35%,
      rgba(111,143,74,0.3) 65%,
      rgba(236,232,227,0) 100%);
  }
  .model-photo {
    position: absolute;
    left: 95px; top: 88px;
    width: 400px; height: 539px;
    background: linear-gradient(180deg,
      var(--photo-dark) 0%,
      var(--photo-mid) 30%,
      var(--photo-light) 60%,
      var(--photo-mid) 90%,
      #2a2a2a 100%);
    border-radius: 120px 120px 0 0;
  }
  .ghost-word {
    position: absolute;
    left: 1100px; top: 365px;
    transform: translate(-50%, -50%) rotate(90deg);
    font-family: "Old Standard TT", serif;
    font-weight: 700;
    font-size: 92px;
    letter-spacing: 10px;
    color: var(--ghost-text);
    white-space: nowrap;
  }
  .headline {
    position: absolute;
    left: 795px; top: 180px;
    transform: translateX(-50%);
    text-align: center;
    white-space: nowrap;
  }
  .headline-script {
    display: block;
    font-family: "Playball", cursive;
    font-size: 62px;
    line-height: 72px;
    color: var(--script-red);
    letter-spacing: 4px;
  }
  .headline-main {
    display: block;
    font-family: "Old Standard TT", serif;
    font-weight: 700;
    font-size: 60px;
    line-height: 66px;
    letter-spacing: 6px;
    color: var(--headline-green);
  }
  .cta-button {
    position: absolute;
    left: 684px; top: 438px;
    width: 220px; height: 56px;
    background: var(--button-black);
    color: var(--button-text);
    font-family: "Old Standard TT", serif;
    font-weight: 700;
    font-size: 15px;
    letter-spacing: 2.5px;
    display: flex;
    align-items: center;
    justify-content: center;
    text-decoration: none;
  }
</style>
</head>
<body>
  <div class="banner">
    <div class="floral-border" role="img" aria-label="Autumn leaves and berries ornament in orange, yellow and green along the top edge"></div>
    <div class="ghost-word" aria-hidden="true">SWEATER</div>
    <div class="model-photo" role="img" aria-label="Photo of two women wearing oversized knit turtleneck sweaters in lilac and grey"></div>
    <h1 class="headline">
      <span class="headline-script">Our Best</span>
      <span class="headline-main">SWEATER</span>
      <span class="headline-script">Ever!</span>
    </h1>
    <a class="cta-button" href="#">SHOP THE LOOK</a>
  </div>
</body>
</html>
```